Email Signature Design

Please design an email signature, the below is an example of our current design;
___

HARCOURT ESTATE PARTNERS PTY LTD
DOMINIC FARRADAY
Licensed Strata and Community Manager

148 Calloway Street,
KELSWORTH NSW 2093

P: 02.9374.6082 F: 9463.7820
Website: www.harcourtestate.com.au

This e-mail message and accompanying data may contain information that is confidential and private. If you are not the intended recipient, the use, dissemination, distribution or copying of this message or data is prohibited.

If you have received this e-mail in error please notify us immediately and delete all material pertaining to this e-mail. strata@harcourtestate.com.au

___

We would like to incorporate our logo and company colours, you can view the colours and feel of image at www.harcourtestate.com.au

Industry/Entity Type

It Company

Requirements
Must have
• use of logo and company colours (image)

```html
<!DOCTYPE html>
<html lang="en">
<head>
<meta charset="utf-8">
<title>Harcourt Estate Partners – Email Signature</title>
<link rel="stylesheet" href="https://fonts.googleapis.com/css2?family=Source+Sans+3:wght@400;600;700&display=swap">
<style>
  :root {
    --olive: #7f7b3c;
    --grey: #6d6e71;
    --text: #5c5d60;
    --ink: #1d1d1d;
    --paper: #ffffff;
    --rule: #9a9a9c;
  }
  * { margin: 0; padding: 0; box-sizing: border-box; }
  html, body { width: 1200px; height: 440px; overflow: hidden; background: var(--paper); }
  body { font-family: "Source Sans 3", sans-serif; color: var(--text); position: relative; }

  .brand-mark { position: absolute; left: 40px; top: 52px; width: 112px; height: 112px; background: var(--olive); }
  .brand-name { position: absolute; left: 33px; top: 178px; font-weight: 700; font-size: 24.6px; letter-spacing: 0.3px; color: var(--grey); line-height: 1; white-space: nowrap; }
  .brand-tagline { position: absolute; left: 33px; top: 205px; font-size: 19px; letter-spacing: 0.6px; color: var(--grey); line-height: 1; white-space: nowrap; }

  .divider { position: absolute; left: 417px; top: 52px; height: 172px; border-left: 1.5px dashed var(--rule); }

  .contact { position: absolute; left: 468px; top: 46px; font-size: 19px; line-height: 22px; white-space: nowrap; }
  .contact-name { font-weight: 700; font-size: 21px; line-height: 21px; color: var(--olive); letter-spacing: 0.4px; }
  .contact-role { margin-top: 7px; }
  .contact-email { color: var(--olive); }
  .contact-email b, .contact-phones b { font-weight: 600; }
  .contact-address { margin-top: 17px; }
  .contact-phones { display: flex; }
  .contact-phones span { display: inline-block; }
  .phone-mobile { color: var(--olive); width: 158px; }
  .phone-office { width: 152px; }
  .contact-phones b { color: var(--olive); }
  .contact-web { font-weight: 700; margin-top: 22px; color: var(--grey); }

  .shadow-rule { position: absolute; left: 47px; top: 278px; width: 1096px; height: 10px;
    background: radial-gradient(ellipse at center top, rgba(60,60,60,0.75) 0%, rgba(120,120,120,0.35) 35%, rgba(255,255,255,0) 70%); }

  .disclaimer { position: absolute; left: 31px; top: 306px; width: 1160px; font-size: 18.3px; line-height: 22.5px; color: var(--ink); white-space: nowrap; }
  .disclaimer strong { font-weight: 700; }
</style>
</head>
<body>
  <div class="brand-mark"></div>
  <div class="brand-name">HARCOURT ESTATE PARTNERS</div>
  <div class="brand-tagline">STRATA MANAGEMENT SERVICES</div>

  <div class="divider"></div>

  <div class="contact">
    <div class="contact-name">DOMINIC FARRADAY</div>
    <div class="contact-role">Licensed Strata and Community Manager</div>
    <div class="contact-email"><b>E</b>: dominic.farraday@harcourtestate.com.au</div>
    <div class="contact-address">148 Calloway Street, KELSWORTH NSW 2093</div>
    <div class="contact-phones">
      <span class="phone-mobile"><b>M</b>: 02.9158.3046</span>
      <span class="phone-office"><b>P</b>: 02.9374.6082</span>
      <span class="phone-fax"><b>F</b>: 02.9463.7820</span>
    </div>
    <div class="contact-web">www.harcourtestate.com.au</div>
  </div>

  <div class="shadow-rule"></div>

  <p class="disclaimer">This e-mail message and accompanying data may contain information that is confidential and private. If you are not the intended recipient, the use,<br>dissemination, distribution or copying of this message or data is prohibited.&nbsp; If you have received this e-mail in error please notify us immediately<br>and delete all material pertaining to this <strong>e-mail. strata@harcourtestate.com.au</strong></p>
</body>
</html>
```